Why engage Insight Harbor?

We are starting a new company that will perform usability consulting and offer usability lab rental. We are in need a one page description flyer.
Updates

Wow! We saw some very interesting and creative flyers posted for review in our contest.

Unfortunately, my schedule became a bit crazy and I may not get back to evaluating them until next week :(  In the meantime, I did want to say thank you for your entries!

Cheers!
Marla

Target Market(s)

product designers, human factors/usability researchers, consumer researcher firms, etc

Industry/Entity Type

It Company

Requirements
Must have
• We would like to see designs with a simple, yet modern, sophisticated feel. I will include our logo images that need to be incorporated along with the font used.

The file called flyer.pdf has all of the information that needs to be included.

Please include 1-3 appropriate stock photos. Please see text in flyer.pdf for description of our services.

Nice to have
• Additionally, there is a sample flyer design that we like for reference. Not a requirement...it is just a reference for the kind of style that we are looking for.

```html
<!DOCTYPE html>
<html lang="en">
<head>
<meta charset="utf-8">
<title>Insight Harbor – Usability Research Flyer</title>
<link rel="stylesheet" href="https://fonts.googleapis.com/css2?family=Source+Sans+3:wght@400;600;700&display=swap">
<style>
  :root {
    --navy: #1f3566;
    --panel-blue: #233c71;
    --green: #8dc63f;
    --orange: #f26522;
    --ink: #2b2b2b;
    --white: #ffffff;
    --photo-dark: #2a2320;
    --photo-warm: #8a5a3a;
  }
  * { box-sizing: border-box; margin: 0; padding: 0; }
  html, body { width: 927px; height: 1200px; overflow: hidden; background: var(--white); }
  body { font-family: "Source Sans 3", Arial, sans-serif; color: var(--ink); }

  .flyer { position: relative; width: 927px; height: 1200px; overflow: hidden; }

  /* Header */
  .header-art {
    position: absolute; left: 570px; top: 0; width: 357px; height: 178px;
    background: radial-gradient(ellipse at 55% 55%, #f4c7a6 0%, #f7e6da 40%, #ffffff 75%);
  }
  .brand {
    position: absolute; left: 50px; top: 68px; z-index: 1;
    display: flex; align-items: center; gap: 14px; white-space: nowrap;
  }
  .brand-dot { width: 30px; height: 30px; border-radius: 50%; background: var(--green); flex: none; }
  .brand-name { font-size: 54px; font-weight: 600; color: var(--navy); letter-spacing: 0.5px; line-height: 1; }
  .address { position: absolute; left: 50px; top: 150px; font-size: 20px; font-weight: 700; color: #111; }

  /* Hero */
  .hero-photo {
    position: absolute; left: 0; top: 189px; width: 603px; height: 405px;
    background: radial-gradient(ellipse at 50% 60%, var(--photo-warm) 0%, #4b3326 45%, var(--photo-dark) 85%);
  }
  .hero-panel {
    position: absolute; left: 603px; top: 189px; width: 324px; height: 405px;
    background: var(--panel-blue); color: var(--white);
    padding: 38px 34px 0 16px; font-size: 18px; line-height: 21.5px;
  }
  .hero-panel p + p { margin-top: 21.5px; }

  /* Benefits */
  .section-title {
    position: absolute; left: 54px; top: 638px;
    font-size: 28px; font-weight: 700; color: var(--green); letter-spacing: 0.3px; line-height: 32px;
  }
  .benefit-column { position: absolute; top: 674px; width: 405px; }
  .benefit-column--left { left: 54px; }
  .benefit-column--right { left: 486px; top: 670px; }
  .benefit { margin-top: 14px; }
  .benefit:first-child { margin-top: 0; }
  .benefit h3 { font-size: 19px; font-weight: 700; color: var(--orange); line-height: 24px; }
  .benefit p { font-size: 13px; line-height: 18px; color: var(--ink); }

  /* Footer */
  .footer { position: absolute; left: 0; top: 1153px; width: 927px; height: 47px; display: flex; }
  .footer-call {
    width: 189px; background: var(--green); color: var(--white);
    font-size: 25px; font-weight: 700; display: flex; align-items: center; justify-content: center;
  }
  .footer-contact {
    flex: 1; background: var(--navy); color: var(--white);
    font-size: 26px; font-weight: 700; display: flex; align-items: center; padding-left: 14px; gap: 16px;
  }
  .footer-square { width: 11px; height: 11px; background: var(--green); }
</style>
</head>
<body>
<main class="flyer">
  <header>
    <div class="header-art" role="img" aria-label="Illustration of small figures with shopping carts around a target, one figure standing in the centre"></div>
    <div class="brand">
      <span class="brand-dot"></span>
      <span class="brand-name">INSIGHT HARBOR</span>
    </div>
    <p class="address">2140 W. Harbor View Lane, Tempe AZ 85281</p>
  </header>

  <section class="hero">
    <div class="hero-photo" role="img" aria-label="Photo of researchers in lab coats looking into a miniature dollhouse with furnished rooms"></div>
    <div class="hero-panel">
      <p>We are a network of human factors engineers, usability specialists, and cognitive/ consumer psychologists, who help you design and evaluate the usefulness, usability and desirability of your products.</p>
      <p>Lease our state of the art consumer research and usability lab, or partner with us on usability testing, eyetracking studies, participatory design, online survey research, ethnographic studies, focus groups and more.</p>
    </div>
  </section>

  <h2 class="section-title">WHY ENGAGE INSIGHT HARBOR?</h2>
  <section class="benefits">
    <div class="benefit-column benefit-column--left">
      <div class="benefit"><h3>Experience</h3><p>Founded by a Professor of Cognitive Psychology and Human Factors with over twenty years of experience, our group includes MS and PhD level consultants with experience working for and consulting with companies like Brightloop, Vantec, Corvida Medical, Pathwell, Meridian Health Hospitals, Hale and Archer, Quantis, and Starfall Studios.</p></div>
      <div class="benefit"><h3>Service</h3><p>Full range of consumer research and usability services, including ethnography, participatory design, questionnaires, user diaries, usability testing, usability evaluation, card sorting, psychometric scaling, focus groups and more.</p></div>
      <div class="benefit"><h3>Range of products and industries</h3><p>Our consultants have extensive experience in design and evaluation of computing, web, tablet, smart phone, product, medical, consumer, and many other types of products and user interfaces.</p></div>
      <div class="benefit"><h3>Client Service Specialist</h3><p>Need copies, printing, lunch, or dinner reservations? Our client service specialist will make sure you have everything you need.</p></div>
      <div class="benefit"><h3>Recruiting</h3><p>Sizable database with ability to recruit research participants</p></div>
    </div>
    <div class="benefit-column benefit-column--right">
      <div class="benefit"><p>according to age, sex, occupation, health status, and other parameters.</p></div>
      <div class="benefit"><h3>Onsite or remote streaming video</h3><p>Sessions can be viewed in many ways: Through our observation mirror, in our meeting room via pan-tilt-zoom camera, at your site on your computer, on your tablet or phone.</p></div>
      <div class="benefit"><h3>Audio/video</h3><p>On-site video editing. Highlight video included in facility rental.</p></div>
      <div class="benefit"><h3>Office space</h3><p>Meeting room for work, phone calls and conference calls. Wireless Internet.</p></div>
      <div class="benefit"><h3>Accessibility</h3><p>Located on the first floor, with ample, free, convenient and handicap parking. Adjustable artificial and natural lighting.</p></div>
      <div class="benefit"><h3>Transcription</h3><p>Transcription services and word frequency key-words-in-context, and word co-occurrence analyses available</p></div>
      <div class="benefit"><h3>Bilingual</h3><p>Several consultants fluent in both English and Spanish</p></div>
    </div>
  </section>

  <footer class="footer">
    <div class="footer-call">CALL NOW</div>
    <div class="footer-contact">
      <span class="footer-phone">480.555.0147</span>
      <span class="footer-square"></span>
      <span class="footer-web">WWW.INSIGHT-HARBOR.COM</span>
    </div>
  </footer>
</main>
</body>
</html>
```